Bespoke Builders Business Card Design

We need a business card for an established builder of high quality bespoke homes in Auckland and Northland. We build and renovate homes collaboratively facilitating effective communication between owners, builders, architects, suppliers and tradespeople. We have never built or renovated a home that leaks or has faults. We only use reliable materials. We have never been sued or had legal action taken against us. We are honest builders of bespoke homes not group mass produced homes. Our niche market is in character homes. We practice sustainability and have built a lot of coastal property. We have been in business for over thirty years . We would like to see natural colors of the environment sand,sea and maybe vegetation . The design should communicate quality, sustainability,fair pricing, open communication and the originality of bespoke building. And the fact that the builder is registered.

Industry/Entity Type

Business

Contact Information for Business Card

Rowan Tellick Builders
Ph. 021583917
18 Kestrel Rd Harwood Bay Auckland 0814
PO Box 927 Mangawhai 0583

```html
<!DOCTYPE html>
<html lang="en">
<head>
<meta charset="utf-8">
<title>Rowan Tellick Builders – Business Card</title>
<link href="https://fonts.googleapis.com/css2?family=Tinos:wght@700&family=Carlito&display=swap" rel="stylesheet">
<style>
  :root {
    --backdrop: #e9e6e2;
    --paper: #fcf9f8;
    --ink: #000000;
    --ink-reverse: #ffffff;
  }
  * { margin: 0; padding: 0; box-sizing: border-box; }
  html, body {
    width: 1189px;
    height: 1200px;
    overflow: hidden;
    background: var(--backdrop);
  }
  .canvas {
    position: relative;
    width: 1189px;
    height: 1200px;
  }
  .card {
    position: absolute;
    left: 140px;
    width: 917px;
    overflow: hidden;
  }
  .card--front {
    top: 45px;
    height: 524px;
    background: var(--paper);
  }
  .card--back {
    top: 624px;
    height: 522px;
    background: var(--ink);
  }
  .front-frame {
    position: absolute;
    left: 0;
    top: 0;
    width: 917px;
    height: 460px;
  }
  .front-band {
    position: absolute;
    left: 0;
    bottom: 0;
    width: 100%;
    height: 64px;
    background: var(--ink);
  }
  .company-name {
    position: absolute;
    left: 0;
    width: 100%;
    text-align: center;
    font-family: "Tinos", "Times New Roman", serif;
    font-weight: 700;
    font-size: 62px;
    line-height: 1;
    white-space: nowrap;
  }
  .card--front .company-name {
    top: 110px;
    left: 18px;
    color: var(--ink);
    font-size: 58px;
  }
  .card--back .company-name {
    top: 232px;
    color: var(--ink-reverse);
  }
  .contact {
    position: absolute;
    left: 18px;
    top: 239px;
    width: 100%;
    text-align: center;
    font-family: "Carlito", "Calibri", sans-serif;
    font-size: 29px;
    line-height: 47px;
    color: var(--ink);
  }
</style>
</head>
<body>
<main class="canvas">
  <section class="card card--front">
    <svg class="front-frame" viewBox="0 0 917 460" aria-hidden="true">
      <path d="M249 416 L54 416 L54 51 L862 51 L862 416 L667 416"
            fill="none" stroke="#000" stroke-width="3.5"/>
      <line x1="158" y1="190" x2="789" y2="190" stroke="#000" stroke-width="1.6"/>
    </svg>
    <h1 class="company-name">Rowan Tellick Builders</h1>
    <address class="contact" style="font-style: normal;">
      <p>021583917</p>
      <p>18 Kestrel Rd Harwood Bay</p>
      <p>Auckland 0814 PO Box 927 Mangawhai 0583</p>
    </address>
    <div class="front-band"></div>
  </section>

  <section class="card card--back">
    <h2 class="company-name">Rowan Tellick Builders</h2>
  </section>
</main>
</body>
</html>
```